Locksmith Business Cards

My father-in-law is in need of new business cards for his locksmith business and I need to impress him. Kindly help me out!

You can see the previous business card attached. It is a family run business in North Wales.

No individual names on the cards.

Key Things to Feature:
- The words "Prompt", "Local", "Reliable" (as you can see under the logo on the website)
- 24h Emergency Service
- Covering All of North Wales, the Wirral and Chester
- The color blue
- A key or a lock would be interesting (similar to the ones that come up when you google locksmith business card)

Optional (only if design includes bullet points, like the example below):
https://imgvaultcdn.net/samples/208314/55172/55172_3904821_208314_image.jpg
- Residential / Commercial / Automotive
- Alarms & Cameras
- Key Cutting & Safes

https://www.brynhafod-locksmiths.co.uk/

Industry/Entity Type

Locksmith

Contact Information for Business Card

01632 960 418
07700 900 362
brynhafodlocksmiths@mailvane.com
Brynhafod Locksmiths, The Willow Barn, 7 Tannery Rd., Llandudno LL99 4QX
www.brynhafod-locksmiths.co.uk

Requirements
Must have
• - The words "Prompt", "Local", "Reliable" (as you can see under the logo on the website)
• - 24h Emergency Service
• - Covering All of North Wales, the Wirral and Chester
Nice to have
• - A key or a lock would be interesting (similar to the ones that come up when you google locksmith business card)

```html
<!DOCTYPE html>
<html lang="en">
<head>
<meta charset="utf-8">
<title>Brynhafod Locksmiths – Business Cards</title>
<link rel="stylesheet" href="https://fonts.googleapis.com/css2?family=Oswald:wght@500&family=Roboto:wght@400;500&display=swap">
<style>
  :root {
    --stage: #2b2b2d;
    --card-dark: #1e1e20;
    --card-dark-mark: #2c2c2f;
    --card-light: #ffffff;
    --brand-blue: #4a5aa8;
    --brand-navy: #26296a;
    --band-start: #4e5fae;
    --band-end: #222467;
    --ink: #3a3a3c;
    --white: #ffffff;
  }
  * { margin: 0; padding: 0; box-sizing: border-box; }
  html, body { width: 1200px; height: 900px; overflow: hidden; background: var(--stage); }
  .canvas { position: relative; width: 1200px; height: 900px; }

  .card { position: absolute; width: 760px; height: 430px; overflow: hidden; }

  /* Back of card */
  .card--back { left: 330px; top: 20px; background: var(--card-dark); }
  .back-mark {
    position: absolute; left: 40px; top: 40px; width: 300px; height: 350px;
    border-radius: 40px; background: linear-gradient(160deg, #38383c, var(--card-dark-mark));
  }
  .back-copy { position: absolute; right: 48px; top: 120px; text-align: right; }
  .back-name {
    font-family: "Oswald", sans-serif; font-weight: 500; color: var(--brand-blue);
    font-size: 48px; line-height: 1.0; letter-spacing: 1px; text-transform: uppercase;
  }
  .back-values, .back-emergency {
    font-family: "Roboto", sans-serif; font-weight: 500; color: var(--brand-blue);
    font-size: 19px; letter-spacing: 1px; line-height: 1.2; text-transform: uppercase;
  }
  .back-values { margin-top: 16px; }
  .back-coverage {
    margin-top: 10px; font-family: "Roboto", sans-serif; font-weight: 400;
    color: var(--white); font-size: 19px; line-height: 1.3; text-align: center;
  }

  /* Front of card */
  .card--front { left: 110px; top: 450px; background: var(--card-light); }
  .services {
    position: absolute; left: 40px; top: 28px;
    font-family: "Roboto", sans-serif; font-size: 19px; line-height: 1.3; color: var(--ink);
  }
  .contacts { position: absolute; left: 40px; top: 128px; list-style: none; }
  .contacts li {
    display: flex; align-items: center; gap: 12px;
    font-family: "Roboto", sans-serif; font-size: 20px; color: var(--ink); line-height: 1.6;
  }
  .contacts svg { width: 20px; height: 20px; fill: var(--brand-navy); flex: none; }

  .brand { position: absolute; right: 40px; top: 168px; display: flex; align-items: center; gap: 16px; }
  .brand-square { width: 70px; height: 70px; border-radius: 10px; background: var(--brand-navy); }
  .brand-name {
    font-family: "Oswald", sans-serif; font-weight: 500; color: var(--brand-navy);
    font-size: 40px; line-height: 1.05; text-transform: uppercase;
  }

  .band { position: absolute; left: 0; bottom: 0; width: 760px; height: 200px; }
  .address {
    position: absolute; right: 40px; bottom: 14px; display: flex; align-items: center; gap: 12px;
    font-family: "Roboto", sans-serif; font-size: 20px; line-height: 1.4; color: var(--white); text-align: right;
  }
  .address svg { width: 20px; height: 26px; fill: var(--white); }
</style>
</head>
<body>
<main class="canvas">

  <section class="card card--back" aria-label="Business card back">
    <div class="back-mark" role="img" aria-label="Large faint brand mark area"></div>
    <div class="back-copy">
      <h1 class="back-name">Brynhafod<br>Locksmiths</h1>
      <p class="back-values">Prompt - Local - Reliable</p>
      <p class="back-emergency">24H Emergency Service</p>
      <p class="back-coverage">Covering All of<br>North Wales The Wirral and Chester</p>
    </div>
  </section>

  <section class="card card--front" aria-label="Business card front">
    <p class="services">Residential | Commercial | Automotive<br>Alarms &amp; Cameras<br>Key Cutting &amp; Safes</p>

    <ul class="contacts">
      <li><svg viewBox="0 0 24 24"><path d="M6.6 10.8a15 15 0 0 0 6.6 6.6l2.2-2.2a1 1 0 0 1 1-.25 11.4 11.4 0 0 0 3.6.57 1 1 0 0 1 1 1V20a1 1 0 0 1-1 1A17 17 0 0 1 3 4a1 1 0 0 1 1-1h3.5a1 1 0 0 1 1 1c0 1.25.2 2.45.57 3.57a1 1 0 0 1-.25 1z"/></svg>01632 960 418</li>
      <li><svg viewBox="0 0 24 24"><path d="M6.6 10.8a15 15 0 0 0 6.6 6.6l2.2-2.2a1 1 0 0 1 1-.25 11.4 11.4 0 0 0 3.6.57 1 1 0 0 1 1 1V20a1 1 0 0 1-1 1A17 17 0 0 1 3 4a1 1 0 0 1 1-1h3.5a1 1 0 0 1 1 1c0 1.25.2 2.45.57 3.57a1 1 0 0 1-.25 1z"/></svg>07700 900 362</li>
      <li><svg viewBox="0 0 24 24"><path d="M2 5h20v14H2z M2 5l10 8 10-8" /></svg>brynhafodlocksmiths@mailvane.com</li>
      <li><svg viewBox="0 0 24 24"><circle cx="12" cy="12" r="10"/></svg>www.brynhafod-locksmiths.co.uk</li>
    </ul>

    <div class="brand">
      <span class="brand-square" aria-hidden="true"></span>
      <span class="brand-name">Brynhafod<br>Locksmiths</span>
    </div>

    <svg class="band" viewBox="0 0 760 200" preserveAspectRatio="none" aria-hidden="true">
      <defs>
        <linearGradient id="bandFill" x1="0" y1="0" x2="1" y2="0">
          <stop offset="0" stop-color="var(--band-start)"/>
          <stop offset="1" stop-color="var(--band-end)"/>
        </linearGradient>
      </defs>
      <path d="M0 80 C110 105 200 135 300 138 C420 140 580 105 760 75 V200 H0 Z" fill="url(#bandFill)"/>
      <path d="M0 66 C110 92 200 122 290 126" fill="none" stroke="var(--band-start)" stroke-width="6"/>
      <path d="M0 80 C110 105 200 135 300 138" fill="none" stroke="var(--white)" stroke-width="6"/>
    </svg>

    <p class="address">
      <span>The Willow Barn, 7, Tannery Rd.<br>Llandudno LL99 4QX</span>
      <svg viewBox="0 0 20 26"><path d="M10 0a10 10 0 0 0-10 10c0 7 10 16 10 16s10-9 10-16A10 10 0 0 0 10 0zm0 14a4 4 0 1 1 0-8 4 4 0 0 1 0 8z"/></svg>
    </p>
  </section>

</main>
</body>
</html>
```